New Innovative Counselling and psychotherapy Service needs Business Card design

Keep it simple and professional. On one side, just company name and logo (perhaps in all blue) and maybe a tag line.

On other side (all white) my name and Qualifications in centre

Industry/Entity Type

Health And Wellness

Contact Information for Business Card

Dara Whelby
Counsellor & Psychotherapist
BSc (Psychol.), BA, Dip. (Couns. & Psych.), PG.Cert (CBT), FGTrK, ONRE

I will also require Mobile no, Email and web site address of which I'll pass on to final designer.

Font styles to use
Sans Serif

Requirements
Must have
• My Logo Only and please use the colours in logo that is in it.
Should not have
• Any other images

```html
<!DOCTYPE html>
<html lang="en">
<head>
<meta charset="UTF-8">
<title>ThriveLane Business Card</title>
<link href="https://fonts.googleapis.com/css2?family=Work+Sans:wght@300;400;500;600&display=swap" rel="stylesheet">
<style>
  :root {
    --backdrop: #2a2a2a;
    --card: #1e1e1e;
    --blue: #4fb3e6;
    --green: #8cc63f;
    --white: #f2f2f2;
  }
  * { margin: 0; padding: 0; box-sizing: border-box; }
  html, body {
    width: 1200px;
    height: 900px;
    overflow: hidden;
    background: var(--backdrop);
    font-family: "Work Sans", sans-serif;
    color: var(--white);
  }
  .stage {
    width: 1200px;
    height: 900px;
    display: flex;
    flex-direction: column;
    align-items: center;
    justify-content: center;
    gap: 30px;
  }
  .card {
    width: 700px;
    height: 400px;
    background: var(--card);
    position: relative;
  }
  /* Brand side */
  .card--brand {
    display: flex;
    flex-direction: column;
    align-items: center;
    justify-content: center;
  }
  .brand-lockup {
    display: flex;
    align-items: center;
    gap: 18px;
    margin-top: 20px;
  }
  .brand-dot {
    width: 44px;
    height: 44px;
    border-radius: 50%;
    background: var(--blue);
  }
  .brand-name--large {
    font-size: 52px;
    font-weight: 400;
    color: var(--blue);
    letter-spacing: 0.5px;
  }
  .website--brand {
    position: absolute;
    bottom: 52px;
    left: 0;
    right: 0;
    text-align: center;
    font-size: 17px;
    letter-spacing: 0.8px;
  }
  .accent { color: var(--green); }
  /* Contact side */
  .card--contact {
    display: flex;
    align-items: center;
    padding: 0 40px 0 60px;
  }
  .brand-lockup--small {
    display: flex;
    align-items: center;
    gap: 14px;
    width: 290px;
  }
  .brand-dot--small { width: 36px; height: 36px; }
  .brand-name--small {
    font-size: 30px;
    font-weight: 300;
    color: var(--white);
  }
  .divider {
    width: 3px;
    height: 190px;
    background: var(--green);
    margin-right: 24px;
  }
  .details { display: flex; flex-direction: column; }
  .person-name {
    font-size: 34px;
    font-weight: 500;
    color: var(--blue);
    text-transform: uppercase;
    line-height: 1;
    margin-bottom: 8px;
  }
  .person-role, .qualifications {
    font-size: 17px;
    line-height: 1.3;
    letter-spacing: 0.4px;
  }
  .contact-list {
    list-style: none;
    margin-top: 12px;
  }
  .contact-list li {
    display: flex;
    align-items: center;
    gap: 10px;
    font-size: 18px;
    line-height: 1.55;
    letter-spacing: 0.5px;
  }
  .contact-icon { width: 14px; height: 14px; flex: none; }
</style>
</head>
<body>
  <main class="stage">
    <section class="card card--brand">
      <div class="brand-lockup">
        <span class="brand-dot"></span>
        <span class="brand-name--large">ThriveLane</span>
      </div>
      <p class="website--brand">www.<span class="accent">thrivelane</span>.com</p>
    </section>

    <section class="card card--contact">
      <div class="brand-lockup--small">
        <span class="brand-dot brand-dot--small"></span>
        <span class="brand-name--small">ThriveLane</span>
      </div>
      <div class="divider"></div>
      <div class="details">
        <h1 class="person-name">Dara Whelby</h1>
        <p class="person-role">Counsellor &amp; Psychotherapist</p>
        <p class="qualifications">BSc (Psychol.), BA, Dip.<br>(Couns. &amp; Psych.), PG.Cert<br>(CBT), FGTrK, ONRE</p>
        <ul class="contact-list">
          <li>
            <svg class="contact-icon" viewBox="0 0 24 24" fill="none" stroke="#4fb3e6" stroke-width="2.2" stroke-linecap="round"><path d="M5 3h4l2 5-2.5 1.5a11 11 0 0 0 6 6L16 13l5 2v4a2 2 0 0 1-2 2A17 17 0 0 1 3 5a2 2 0 0 1 2-2z"/></svg>
            888-555-0147
          </li>
          <li>
            <svg class="contact-icon" viewBox="0 0 24 24" fill="none" stroke="#4fb3e6" stroke-width="2.2"><rect x="3" y="5" width="18" height="14" rx="1"/><path d="M3 6l9 7 9-7"/></svg>
            info@thrivelane.com
          </li>
          <li>
            <svg class="contact-icon" viewBox="0 0 24 24" fill="none" stroke="#4fb3e6" stroke-width="2"><circle cx="12" cy="12" r="9"/><path d="M3 12h18M12 3c3 3 3 15 0 18M12 3c-3 3-3 15 0 18"/></svg>
            www.<span class="accent">thrivelane</span>.com
          </li>
        </ul>
      </div>
    </section>
  </main>
</body>
</html>
```